Business Card Design Project

We are looking to redesign the logo, business card and stationary of one of our group companies - SOLARO SUPPLY HOUSE LLC.

The company specialises in industrial PVC and CPVC Piping systems. It is situated in the Middle East and the focus is purely in this region.

The logo work is already completed. The file is uploaded for the reference.

We are looking for a clean minimalistic design for the business card.

regards
Rohit
Updates

Hello Everyone!

Thanks for submitting your designs. 

Yet to find the right design. Probably the below links will give you guys some more idea on what we would like.

Minimalist design with some creativity.

Rohit

http://exampledesignfolio.com/inspiration/15-beautifully-minimal-business-cards

http://www.samplelayoutbase.com/2011/11/14/30-minimalist-business-card-design/

http://www.primepixelcraft.com/inspiration/minimal-business-cards/

Target Market(s)

Industrial users

Industry/Entity Type

Industrial

Requirements
Must have
• - Minimalistic design

- Back side of the card should include the manufacturer PIPEMARQ NORTHERN's decal. The file is upload for the reference

- Further information
Company Name:
SOLARO SUPPLY HOUSE LLC
Address:
PO Box 8152, Sharjah Industrial Area 4, Qarwan Road
Sharjah, United Arab Emirates
Telephone:
+971-6-5000-118
Fax:
+977-6-5000-119
Email:
mail@sshlexample.com

- FYI, Solaro Supply House LLC is the authorised distributor for PIPEMARQ NORTHERN in the UAE. For further information on pipemarq please visit the website www.pipemarq-example.ca

```html
<!DOCTYPE html>
<html lang="en">
<head>
<meta charset="utf-8">
<title>Solaro Supply House LLC – Business Card</title>
<link href="https://fonts.googleapis.com/css2?family=Arimo:wght@700&display=swap" rel="stylesheet">
<style>
  :root {
    --card-bg: #f4f4f4;
    --photo-light: #f7f7f7;
    --photo-mid: #e6e6e6;
    --title-blue: #2f7fc8;
    --contact-blue: #1f58a5;
    --email-blue: #3a80c6;
    --address-grey: #6a6a6a;
    --mark-dark: #1c1c1c;
  }
  * { margin: 0; padding: 0; box-sizing: border-box; }
  html, body {
    width: 1200px;
    height: 686px;
    overflow: hidden;
    background: #ffffff;
  }
  .card {
    position: relative;
    width: 1200px;
    height: 686px;
    background: var(--card-bg);
    font-family: "Arimo", Arial, sans-serif;
    font-weight: 700;
    overflow: hidden;
  }
  .card-backdrop {
    position: absolute;
    inset: 0;
    background: linear-gradient(160deg, var(--photo-light) 0%, #efefef 45%, var(--photo-mid) 100%);
  }
  .company-name {
    position: absolute;
    top: 92px;
    left: 0;
    width: 100%;
    text-align: center;
    font-size: 59px;
    letter-spacing: 0.5px;
    color: var(--title-blue);
    text-shadow: 0 8px 10px rgba(0, 0, 0, 0.22);
  }
  .phone-lines {
    position: absolute;
    left: 54px;
    top: 300px;
    font-size: 30px;
    line-height: 41px;
    color: var(--contact-blue);
  }
  .address {
    position: absolute;
    right: 40px;
    top: 278px;
    text-align: right;
    font-style: normal;
    font-size: 25px;
    line-height: 34px;
    color: var(--address-grey);
  }
  .brand-mark {
    position: absolute;
    left: 566px;
    top: 536px;
    width: 68px;
    height: 68px;
    border-radius: 14px;
    background: var(--mark-dark);
  }
  .email {
    position: absolute;
    top: 628px;
    left: 0;
    width: 100%;
    text-align: center;
    font-size: 25px;
    color: var(--email-blue);
  }
</style>
</head>
<body>
  <main class="card">
    <div class="card-backdrop" role="img" aria-label="Faint background photograph of grey PVC pipe fittings"></div>

    <h1 class="company-name">SOLARO SUPPLY HOUSE LLC</h1>

    <div class="phone-lines">
      <p class="phone">Tel: +971-6-5000-118</p>
      <p class="fax">Fax: +977-6-5000-119</p>
    </div>

    <address class="address">
      PO Box 8152<br>
      Sharjah Industrial Area 4<br>
      Qarwan Road<br>
      Sharjah<br>
      United Arab Emirates
    </address>

    <div class="brand-mark" aria-hidden="true"></div>

    <p class="email">Email: mail@sshlexample.com</p>
  </main>
</body>
</html>
```